Counseling Practice Business Card

I need a professional looking business card incorporating my new logo that was just completed. Card needs to incorporate my name and title, description of my specialty, my address, my phone number, my fax number, my email and my website URL. I need to be able to choose design on/with different paper colors and textures.
I do not have a lot of business card ideas so I am open to anything but I want bold,sharp, clear card without additional designs other than my logo (see attached file info). I am open to different color backgrounds or paper colors including black. I do not like traditional brackets around area codes in phone number or dashes between numbers in phone number. Am open to other ways of presenting including periods between numbers as appropriate. I do not know enough to know what I like yet but I want card to coordinate and work together with my logo. My practice emphasizes natural mental health interventions so any use of color (with background paper color or the blue and green in my logo) that elicits nature is nice. In addition to black, any natural brown or wood looking background might be desirable also. Most of the offerings so far look very similar and boring.

Target Market(s)

Potential therapy clients and other professionals

Contact Information for Business Card

Card information:
Gerald M. Whitcombe, Ph.D.
Licensed Clinical Psychologist
Integrative Health Coach
4812 Marlowe Ridge Blvd SE
Suite 310
Duluth, GA 30096
(770) 415-2983 phone
(770) 581-4096 fax
drgeraldwhitcombe@quillmarsh.net
brightfernwellness.net

Font styles to use
Serif
Sans Serif
Other font styles liked:
• anything that you think looks crisp, clear and easily readable

Requirements
Must have
• Any color used should coordinate with my logo design (see attached files).
• Card should be printed horizontally so top and bottom are longest sides of rectangle.
• Background color or paper color should complement and highlight logo. Do not like a white background. black, grey, brown or any color my logo would blend well with.
Nice to have
• I would like designer to utilize color to highlight letters/name or phone-fax-web symbols.
• Bottom edge of card could be highlighted if appropriate to an idea.
Should not have
• I would NOT want the card to have a pure white background at all.
• No clear cards.
• Cards should be oriented with long sides on bottom and top, NOT sides. DO NOT LIKE THIS THIN TALL ORIENTATION.

```html
<!DOCTYPE html>
<html lang="en">
<head>
<meta charset="utf-8">
<title>Brightfern Wellness – Business Card</title>
<link href="https://fonts.googleapis.com/css2?family=Roboto:wght@400;500&family=Roboto+Condensed:wght@700&display=swap" rel="stylesheet">
<style>
  :root {
    --backdrop: #c98a4f;
    --card: #131416;
    --brand-blue: #2a73b8;
    --brand-green: #1f7a3c;
    --text-grey: #d4d6d8;
    --rule-grey: #4a4c50;
    --url-grey: #c8c9cb;
  }
  * { margin: 0; padding: 0; box-sizing: border-box; }
  html, body { width: 1200px; height: 960px; overflow: hidden; }
  body {
    position: relative;
    background: var(--backdrop);
    font-family: "Roboto", Arial, sans-serif;
  }
  .card {
    position: absolute;
    width: 600px;
    height: 342px;
    background: var(--card);
    box-shadow: 0 4px 10px rgba(0,0,0,0.35);
    overflow: hidden;
  }
  .card--front { left: 314px; top: 113px; }
  .card--back { left: 311px; top: 472px; }

  .practice-name {
    position: absolute;
    color: var(--brand-blue);
    font-family: "Roboto", Arial, sans-serif;
    font-weight: 500;
    white-space: nowrap;
  }
  .card--front .practice-name {
    left: 30px; top: 140px;
    font-size: 27px;
  }
  .card--back .practice-name {
    left: 0; right: 0; top: 140px;
    text-align: center;
    font-size: 46px;
  }

  .details { position: absolute; left: 311px; top: 58px; }
  .person-name {
    font-family: "Roboto Condensed", "Arial Narrow", sans-serif;
    font-weight: 700;
    font-size: 20px;
    color: var(--brand-blue);
    text-transform: uppercase;
    line-height: 24px;
  }
  .person-title {
    color: var(--brand-green);
    font-size: 15px;
    line-height: 19px;
    letter-spacing: 0.2px;
  }
  .address {
    margin-top: 9px;
    color: var(--text-grey);
    font-size: 14px;
    line-height: 18px;
    font-style: normal;
  }
  .contact-list { list-style: none; margin-top: 12px; }
  .contact-list li {
    display: flex; align-items: center;
    color: var(--text-grey);
    font-size: 14px; line-height: 19px;
  }
  .contact-list svg { width: 13px; height: 13px; margin-right: 10px; fill: var(--brand-blue); }

  .bottom-rule {
    position: absolute; left: 0; right: 0; top: 308px;
    height: 1px; background: var(--rule-grey);
  }
  .url-band {
    position: absolute; left: 299px; top: 292px;
    width: 269px; height: 30px;
    background: var(--brand-blue);
    color: #e6eef6;
    font-size: 14px; line-height: 30px;
    padding-left: 24px;
  }
  .back-url {
    position: absolute; left: 0; right: 0; top: 284px;
    text-align: center;
    color: var(--url-grey);
    font-size: 14px;
    letter-spacing: 4px;
  }
</style>
</head>
<body>
  <section class="card card--front">
    <div class="practice-name">Brightfern Wellness</div>

    <div class="details">
      <h1 class="person-name">Gerald M. Whitcombe, Ph.D.</h1>
      <p class="person-title">Licensed Clinical Psychologist</p>
      <p class="person-title">Integrative Health Coach</p>
      <address class="address">
        4812 Marlowe Ridge Blvd SE<br>
        Suite 310<br>
        Duluth, GA 30096
      </address>
      <ul class="contact-list">
        <li>
          <svg viewBox="0 0 16 16" aria-hidden="true"><path d="M3.6 1 6 3.6 4.7 5.6c.9 2 2.6 3.7 4.6 4.6l2-1.3L14 11.4 12.6 15C6.4 14.6 1.4 9.6 1 3.4Z"/></svg>
          (770) 415-2983
        </li>
        <li>
          <svg viewBox="0 0 16 16" aria-hidden="true"><path d="M4 1h8v4H4ZM1 6h14v6h-2v-2H3v2H1Zm3 5h8v4H4Z"/></svg>
          (770) 581-4096
        </li>
        <li>
          <svg viewBox="0 0 16 16" aria-hidden="true"><path d="M1 3h14v1.2L8 9 1 4.2Zm0 2.6 7 4.8 7-4.8V13H1Z"/></svg>
          drgeraldwhitcombe@quillmarsh.net
        </li>
      </ul>
    </div>

    <div class="bottom-rule"></div>
    <div class="url-band">www.brightfernwellness.net</div>
  </section>

  <section class="card card--back">
    <div class="practice-name">Brightfern Wellness</div>
    <p class="back-url">www.brightfernwellness.net</p>
  </section>
</body>
</html>
```